Website front end design for an education nonprofit

This project involves design and development of the website front end (i.e., Web user interface and user experience design) for TAVO Sphere, a nonprofit initiative for developing an online platform for basic English language instruction, especially targeted toward underprivileged, non-native English speaking populations.

More about us: We are a team of educators, researchers and engineers passionate about this cause and would like to invite talented, creative web developers to join us in this effort to create positive social impact! Please send a personal message to the project owner for the executive summary to get more information about our initiative, big picture vision and the team.

TAVO Sphere website front end (UI/UX) design
Our key goals for this project are to develop an impressive Drupal-based front end for our website as well as to find really talented and creative web/UI/UX designers-cum-developers who are experts in the state-of-the-art web technologies, and are passionate about the cause of global online basic education. At the end of this project, we hope to have long term engagement with the selected developer(s) for our future website design and development needs.

Here are some preliminary guidelines on the TAVO Sphere website front end framework as envisioned by us so far. Please note that we would very much encourage creative ideas and mock-ups from the developers.

1. Current platform: Our website prototype back-end uses Drupal CMS (we plan to continue using Drupal CMS) and at the moment, a toy front-end is based on the Drupal Skeleton platform for its simplicity, clean UI and mobile device friendliness. The web developer / designer can choose any Drupal front end as a starting point or come up with a new Drupal template that meets our requirements below. Prior experience and expertise on Drupal would be great.

2. Audience profile: While the primary audience for the website is expected to be young kids (6-10 years) not very familiar with English, the secondary audience also includes adults interested in basic English language skills. So the overall goal is to have simple, uncluttered / clean, elegant and lightweight (think loading time as well as mobile device friendliness) interface that is extremely intuitive and easy to navigate, is artistic and aesthetically appealing to a wide audience (especially the non-native English speaking populations). The most important point is that our target audience should feel welcome with the clean, crisp look and easy, user-centric navigation, and should in no case feel overwhelmed (say with too much text or clutter on the front page).

3. Front page: Here is a currently envisioned preliminary sketch of the website front page (very much open for refinement and improvements)
a. The top “menu bar” part of the landing page will have our organization name and logo along with (or above) the top menu bar with the following links and sub-links
i. “Learn” link with sub-menu of all our content sections (World learning, Basic sentence learning, Classic short stories, Picture Dictionary)
ii. “About” links with information about us (sub-menu entries: About TAVO Sphere, Team, Supporters, Contributors)
iii. “Contribute” link with sub-menu entries Donate, Volunteer
iv. Menu entries towards the right side: “Login / sign up” followed by
v. “Search” with space to enter the search phrase
b. The middle “main page content” part of the page is where we would have entry points to our main content categories. The portion is envisioned to be graphical, with big blocks (images) as links to our content categories. The current categories (to start with) include 1. Word learning, 2. Basic sentence learning, and 3. Classic stories. We welcome creative ideas to represent these content categories in an appealing and elegant way (for example, these content categories could be portrayed as closed double doors that lead to the pages with the content. We would like to have placeholders for appropriate image links to different content categories – we should be able to put appropriate images or change them as we come up with new ideas that would work best with our target audience). The categories would change and grow as our content evolves, hence the core idea is to build a flexible framework that readily allows for expansion as well as customization.
c. The bottom menu / links bar portion of the landing page will have a list of links that are not included at the top. Examples include (with flexibility needed to add more when needed)
i. “Help”: this leads to a new page with FAQ, How to use
ii. “Contact us” link to a web contact form page
iii. “For Teachers” link to a page with information such as how to use, tips, pilot programs,
iv. “Volunteer” link to page with links such as Donate, Volunteer
v. “Contributors” that would link to a page with information about our Artists, Teachers, Writers, Developers etc.
vi. “Jobs” would link to a jobs page
vii. “Blog” would lead to our blog page
viii. “User stories” link to pages with feedback that we obtain from the users about how the content has helped them,
ix. Web 2.0 placeholders for social media (to be added later)

d. The footer of the website should include text “2013 TAVO Sphere, All rights reserved.”

4. The middle block of the front page is the largest in screen real estate and perhaps the most challenging part that requires much creativity and thought on the UI/UX design aspect – the content pages pointed to by the section links on the middle portion of the front page are also being designed.

5. Color preference is towards soft, elegant (think grays, whites, light blues, other light colors) web safe colors. No harsh (too bright, garish) colors.

6. Fonts preference Nice, clean looking fonts (Arial alright) compatible across browsers.

7. Portability and robustness of the front page layout for different platforms should be carefully considered. Although our first launch target platform is PC (where cross browser compatibility is important), this would very soon be followed by mobile devices such as tablets and smartphones given their prevalence across the globe. This mobile friendly design or easy portability to mobile platforms with little work requirement should be considered as a design requirement.

8. Front page as a framework for the complete website: Note that the top and the bottom portions of the front page are envisioned be used as a common template / frame across all the pages of our website – the middle portion would be used to show our content on the other pages of our website.

9. UX: For the UI/UX design, it is critical to keep in mind key qualities such as ease of use, simplicity, elegance and artistic appeal. Some specific points to keep in mind: (1) the major portion of the target audience would be new to English and (2) young children are expected to be the primary audience but we want the website to appeal to adults interested in learning as well, and (3) we need the website to work even with relatively slow Internet speeds (for underdeveloped / developing regions especially), should always be kept in mind. HTML5 compliance ideas are encouraged.

10. Strictly not desired: Typical corporate feel seen in many webpages, blocky graphics, dull and uninviting overall look with no personality, Flash type effects, harsh colors.

11. Creativity and imagination necessary: We would like to reiterate that the designer/developer has complete freedom to re-imagine the front page considering the above requirements and get back with ideas for an inspiring layout that presents the content outlined above in an intuitive format, carefully considering our target audience.

A note: As a rule, we will always make sure that our developers and artists get proper credit for their work and are recognized and acknowledged by everyone visiting our website.

Expected deliverables:
Website design psd files AND coded webpage / Drupal template: the corresponding source code and all the required libraries, images etc would be required with minimal documentation / pointers on how to make changes and customizations.

Interested developers are encouraged to first send us preliminary prototype Design for the front page to get feedback on whether their approach and style is in line with our needs and preferences. We will suggest the developers to proceed further if the team thinks there is some potential for a match (of course, the final determination would be from the pool of shortlisted submissions) – otherwise, in case the team does not see potential for a match with our needs or if we have already received multiple submissions that are comparatively more closely aligned with our vision for the website, we'd prefer to be respectful of the developers’ time and effort by requesting them not to proceed further.

Please consider this effort as your contribution to an important social cause of global and accessible online education and not a commercial enterprise (our passion for making a positive impact is what is driving the TAVO Sphere nonprofit team to undertake this initiative!). We would like to invite you to join us in this effort!

Project Deadline Extended
Reason: Due to requests from interested designers, we are extending the deadline. Looking forward to receiving many other creative designs!

Please see the project brief.

Real Estate

• Please see the project brief.

```html
<!DOCTYPE html>
<html lang="en">
<head>
<meta charset="utf-8">
<title>TAVO Sphere – Learn English</title>
<link href="https://fonts.googleapis.com/css2?family=Arimo:wght@400;700&family=Noto+Serif&family=Open+Sans:wght@400&display=swap" rel="stylesheet">
<style>
:root{
  --blue:#4db0e0;
  --blue-deep:#2a9fd4;
  --ink:#333;
  --text:#555;
  --muted:#777;
  --header:#f2f2f2;
  --footer:#f4f4f4;
  --line:#dcdcdc;
}
*{margin:0;padding:0;box-sizing:border-box}
html,body{width:933px;height:1200px;overflow:hidden;background:#fff}
body{position:relative;font-family:"Arimo",Arial,sans-serif;color:var(--text)}
.abs{position:absolute}
a{color:inherit;text-decoration:none}

.topline{left:0;top:0;width:933px;height:3px;background:var(--blue)}
.header{left:0;top:3px;width:933px;height:103px;background:var(--header);border-bottom:2px solid #e2e2e2;box-shadow:0 2px 3px rgba(0,0,0,.06)}
.brand{left:102px;top:36px;font-family:"Noto Serif",serif;font-size:32px;letter-spacing:.5px;color:var(--blue);line-height:1}
.account{right:101px;top:12px;font-size:9px;color:var(--ink);letter-spacing:.3px}
.account span{margin:0 6px;color:#999}
.search{left:664px;top:38px;width:168px;height:24px;background:#fff;border:1px solid #e3e3e3;border-radius:12px;font-size:8.5px;color:#aaa;padding:7px 0 0 13px}
.search svg{position:absolute;right:8px;top:4px}
.nav{top:82px;font-size:10.5px;font-weight:700;color:var(--ink);letter-spacing:.4px}
.nav .caret{display:inline-block;width:8px;height:2px;background:var(--blue);margin-left:6px;vertical-align:middle}
.learn-tab{left:467px;top:71px;width:85px;height:40px;background:var(--blue);border-radius:14px 14px 0 0;color:#233;font-size:10.5px;font-weight:700;text-align:center;padding-top:12px;letter-spacing:.4px}
.dropdown{left:467px;top:104px;width:147px;height:90px;background:var(--blue);border-radius:0 0 16px 16px;box-shadow:0 2px 4px rgba(0,0,0,.12);padding:10px 0 0 22px;z-index:3}
.dropdown a{display:block;color:#fff;font-size:10.5px;line-height:18.7px}

.slider{left:101px;top:112px;width:731px;height:315px;background:#fff;border:1px solid #ddd;box-shadow:0 1px 3px rgba(0,0,0,.15);padding:3px}
.slide-photo{width:100%;height:100%;background:radial-gradient(ellipse at 60% 30%,#d9a58c 0%,#b86c52 28%,transparent 50%),linear-gradient(180deg,#7c8d3c 0%,#a4a55a 45%,#b34b3b 80%,#8e2e2a 100%)}
.caption{left:122px;top:330px;width:484px;height:79px;background:rgba(255,235,240,.78);padding:8px 12px}
.caption h2{font-family:"Noto Serif",serif;font-weight:400;font-size:27px;color:#222;line-height:32px}
.caption p{font-family:"Open Sans",sans-serif;font-size:11px;line-height:15px;color:#444;margin-top:2px}
.dots{left:749px;top:396px;display:flex;gap:6px}
.dots i{width:13px;height:13px;border-radius:3px;background:rgba(255,255,255,.45)}
.dots i.on{background:#fff}

.section-bar{left:101px;top:453px;width:731px;height:32px;background:#f1f1f1;text-align:center;font-size:16px;font-weight:700;color:var(--ink);line-height:32px;letter-spacing:.5px}
.card{top:496px;width:205px;text-align:center}
.card .thumb{width:205px;height:102px;border-radius:3px}
.card h3{margin-top:17px;font-size:11.5px;color:var(--blue-deep);letter-spacing:.4px}
.card p{margin:6px auto 0;width:210px;font-size:9.7px;line-height:15.5px;color:var(--text);letter-spacing:.1px}
.btn{display:block;width:64px;height:26px;border-radius:13px;background:linear-gradient(#f8f8f8,#e2e2e2);box-shadow:0 1px 2px rgba(0,0,0,.25);font-size:10px;font-weight:700;color:#444;line-height:26px;text-align:center}
.card .btn{position:absolute;left:71px;top:241px}

.rule{left:101px;top:776px;width:731px;height:3px;background:#e4e4e4}
.vrule{left:458px;top:800px;width:1px;height:133px;background:#e2e2e2}
.welcome{left:101px;top:798px;width:345px}
.block-title{font-size:16px;font-weight:400;color:var(--ink)}
.welcome p{margin-top:11px;font-size:9.7px;line-height:15.5px}
.welcome .btn{position:absolute;top:108px}
.contribute{left:474px;top:798px;width:360px}
.item{position:absolute;top:32px;width:170px}
.item .thumb{position:absolute;left:0;top:0;width:68px;height:54px;border:1px solid #e5e5e5;box-shadow:0 1px 2px rgba(0,0,0,.15)}
.item h4{margin-left:78px;font-size:11.5px;color:var(--blue-deep);line-height:12px}
.item p{font-size:9.4px;line-height:15.5px;margin-top:2px}
.item p .indent{display:block;margin-left:78px}

.footer{left:0;top:954px;width:933px;height:200px;background:var(--footer);border-bottom:1px solid #e3e3e3}
.fcol{top:975px}
.fcol h5{font-size:10.5px;color:var(--ink);letter-spacing:.3px;margin-bottom:7px}
.fcol a{display:block;font-size:9.5px;line-height:19.4px;color:var(--text)}
.fcol a::before{content:"";display:inline-block;width:5px;height:5px;border-top:1px solid var(--blue);border-right:1px solid var(--blue);transform:rotate(45deg);margin-right:10px;vertical-align:1px}
.social a::before{display:none}
.social a{display:flex;align-items:center;line-height:25px}
.social i{width:19px;height:19px;border-radius:3px;margin-right:9px;flex:none}
.copy{left:0;top:1172px;width:933px;text-align:center;font-size:8.5px;color:#444}
.copy span{color:var(--blue-deep)}
</style>
</head>
<body>
<div class="abs topline"></div>
<header class="abs header"></header>
<div class="abs brand">TAVO SPHERE</div>
<div class="abs account"><a href="#">LOG IN</a><span>|</span><a href="#">SIGN UP</a></div>
<div class="abs search">Search keyword...
  <svg width="16" height="16" viewBox="0 0 16 16"><circle cx="6" cy="6" r="4.3" fill="none" stroke="#222" stroke-width="1.8"/><line x1="9.2" y1="9.2" x2="14" y2="14" stroke="#222" stroke-width="2.4" stroke-linecap="round"/></svg>
</div>
<div class="abs learn-tab">LEARN</div>
<nav class="abs dropdown">
  <a href="#">Word learning</a><a href="#">Basic sentence learning</a><a href="#">Classic short stories</a><a href="#">Picture Dictionary</a>
</nav>
<div class="abs nav" style="left:574px">ABOUT<span class="caret"></span></div>
<div class="abs nav" style="left:654px">CONTRIBUTE<span class="caret"></span></div>
<div class="abs nav" style="left:765px">CONTACT US</div>

<div class="abs slider"><div class="slide-photo" role="img" aria-label="Child holding wooden letter blocks spelling LEARN on grass"></div></div>
<div class="abs caption">
  <h2>WORD LEARNING</h2>
  <p>Suspendisse lobortis turpis in odio blandit ac interdum lorem euismod. Etiam risus massa, vulputate eu pellentesque et, consectetur a neque.</p>
</div>
<div class="abs dots"><i class="on"></i><i></i><i></i><i></i></div>

<div class="abs section-bar">LEARN</div>

<div class="abs card" style="left:114px">
  <div class="thumb" role="img" aria-label="Coloured paper circles pinned on a cork board with pronouns" style="background:linear-gradient(135deg,#c49468,#e7a0c8 40%,#f2d36a 70%,#b98a5e)"></div>
  <h3>WORD LEARNING</h3>
  <p>Vestibulum vel metus sit amet turpis bibendum tincidunt vel sit amet quam. Pellentesque habi-tant morbi tristique senectus et netus et male-suada fames ac turpis egestas. Nunc conse-quat congue nulla eu imperdiet. Donec in est erat, id malesuada turpis.</p>
  <a class="btn" href="#">MORE</a>
</div>
<div class="abs card" style="left:365px">
  <div class="thumb" role="img" aria-label="Hand writing a question about speaking English on a whiteboard" style="background:linear-gradient(135deg,#eef0f2,#dfe3e6)"></div>
  <h3>BASIC SENTANCE LEARING</h3>
  <p>Vestibulum vel metus sit amet turpis bibendum tincidunt vel sit amet quam. Pellentesque habi-tant morbi tristique senectus et netus et male-suada fames ac turpis egestas. Nunc consequat congue nulla eu imperdiet. Donec in est erat, id malesuada turpis.</p>
  <a class="btn" href="#">MORE</a>
</div>
<div class="abs card" style="left:613px">
  <div class="thumb" role="img" aria-label="Young man holding an English book" style="background:linear-gradient(180deg,#d6d6d6,#c4c4c4 70%,#b9b9bf)"></div>
  <h3>CLASSIC SHORT STORIES</h3>
  <p>Vestibulum vel metus sit amet turpis bibendum tincidunt vel sit amet quam. Pellentesque habi-tant morbi tristique senectus et netus et male-suada fames ac turpis egestas. Nunc consequat congue nulla eu imperdiet. Donec in est erat, id malesuada turpis.</p>
  <a class="btn" href="#">MORE</a>
</div>

<div class="abs rule"></div>
<div class="abs vrule"></div>

<section class="abs welcome">
  <h2 class="block-title">Welcome to TAVO Sphere</h2>
  <p>Aliquam molestie, mi et imperdiet euismod, dui purus auctor tellus, et interdum lacus lectus et ante. Sed accumsan sollicitudin sapien, sit amet adipiscing turpis gravida ac. In congue, neque ac lobortis volutpat, libero mauris varius mi, vitae suscipit ipsum ligula vitae risus.</p>
  <a class="btn" href="#">MORE</a>
</section>

<section class="abs contribute">
  <h2 class="block-title">Contribute</h2>
  <div class="item" style="left:0">
    <div class="thumb" role="img" aria-label="Hand writing a cheque with a pen" style="background:linear-gradient(135deg,#c9a07a,#ece3d6 60%,#f6f2ea)"></div>
    <h4>Donate</h4>
    <p><span class="indent">Aliquam molestie,</span><span class="indent">mi et imperdiet</span><span class="indent">euismod, dui purus</span>vulputate eu pellentesque et, consect-etur a neque.</p>
  </div>
  <div class="item" style="left:189px">
    <div class="thumb" role="img" aria-label="Colourful raised hands" style="background:linear-gradient(90deg,#fff,#e7e0f2 30%,#f5d3d0 60%,#fff)"></div>
    <h4>Volunteer</h4>
    <p><span class="indent">Aliquam molestie,</span><span class="indent">mi et imperdiet</span><span class="indent">euismod, dui purus</span>vulputate eu pellentesque et, consect-etur a neque.</p>
  </div>
</section>

<footer class="abs footer"></footer>
<div class="abs fcol" style="left:102px"><h5>LEARN</h5><a href="#">Word learning</a><a href="#">Basic sentence learning</a><a href="#">Classic short stories</a><a href="#">Picture Dictionary</a></div>
<div class="abs fcol" style="left:256px"><h5>ABOUT</h5><a href="#">About TAVO Sphere</a><a href="#">Team</a><a href="#">Supporters</a><a href="#">Contributors</a></div>
<div class="abs fcol" style="left:413px"><h5>CONTRIBUTE</h5><a href="#">Donate</a><a href="#">Volunteer</a></div>
<div class="abs fcol" style="left:559px"><h5>QUICK LINKS</h5><a href="#">Help</a><a href="#">Contact us</a><a href="#">For teachers</a><a href="#">Volunteer</a><a href="#">Contributors</a><a href="#">Jobs</a><a href="#">Blog</a><a href="#">User stories</a></div>
<div class="abs fcol social" style="left:714px"><h5 style="margin-bottom:2px">CONNECT US</h5>
  <a href="#"><i style="background:#4a6aa5"></i>Circlebook</a>
  <a href="#"><i style="background:#2f7cb0"></i>LinkRing</a>
  <a href="#"><i style="background:#8fd0ea"></i>Chirper</a>
  <a href="#"><i style="background:#f08a2a"></i>Rss Feed</a>
  <a href="#"><i style="background:#444"></i>Globe +</a>
</div>
<div class="abs copy">Copyright © 2013 <span>TAVO Sphere</span>, All rights reserved</div>
</body>
</html>
```